Zestora - Landing Page

Need a landing page for a journal app. The app is based on a retrospective board, where each journal entry is split into 3 sections: "What went well", "What Didn't Go Well" and "Things To Try".
The landing page should match the style of all modern web application landing pages. Think Brint, Tivalo, Mirvane. I've included screenshots of the app.
One feature that I want to highlight that is not ready yet, is an AI coach. It will offer insights based on the history of the user's journal entries
1 page

```html
<!DOCTYPE html>
<html lang="en">
<head>
<meta charset="utf-8">
<title>Zestora – Guided Journaling</title>
<link href="https://fonts.googleapis.com/css2?family=Syne:wght@500;600;700;800&family=Open+Sans:wght@400;600;700&display=swap" rel="stylesheet">
<style>
:root{
  --ink:#1b1b1f;
  --text:#333740;
  --muted:#5a5f6a;
  --blue:#1f6ef0;
  --blue-dark:#1556c4;
  --band:#eef4fd;
  --navy:#1e2b3c;
  --coral:#f7a597;
  --sun:#fde29a;
  --sky:#5b9cf3;
  --line:#dfe3ea;
  --panel:#ececee;
}
*{box-sizing:border-box;margin:0;padding:0}
html,body{width:1200px;height:4149px;overflow:hidden}
body{position:relative;background:#fff;font-family:"Open Sans",Arial,sans-serif;color:var(--text)}
.abs{position:absolute}
.display{font-family:"Syne","Trebuchet MS",sans-serif;color:var(--ink)}
.btn{position:absolute;display:flex;align-items:center;justify-content:center;background:var(--blue);color:#fff;font-weight:700;font-size:16px;border-radius:3px;box-shadow:3px 3px 0 #b9cff5}
/* nav */
.brand{display:flex;align-items:center;gap:12px;font-family:"Open Sans",sans-serif;font-weight:600;color:var(--ink)}
.brand-square{width:34px;height:34px;background:var(--ink);border-radius:2px}
.nav{left:482px;top:50px;display:flex;gap:20px;font-size:14px;color:#444}
.nav .active{color:var(--blue)}
/* bands */
.hero-band{left:0;top:575px;width:1200px;height:600px;background:linear-gradient(var(--band),#f7faff 80%,#fff)}
.coach-band{left:0;top:3300px;width:1200px;height:530px;background:linear-gradient(#fff,var(--band) 30%,var(--band))}
.dots{width:34px;height:34px;background:
 linear-gradient(#c9ccd3,#c9ccd3) 0 0/13px 13px no-repeat,
 linear-gradient(#c9ccd3,#c9ccd3) 21px 0/13px 13px no-repeat,
 linear-gradient(#c9ccd3,#c9ccd3) 0 21px/13px 13px no-repeat,
 linear-gradient(#c9ccd3,#c9ccd3) 21px 21px/13px 13px no-repeat}
/* hero app */
.app{left:193px;top:408px;width:816px;height:467px;background:var(--navy);border-radius:8px;padding:10px 10px 10px 40px;overflow:hidden}
.app-body{background:#fff;width:100%;height:100%;position:relative;overflow:hidden}
.side-icon{position:absolute;left:15px;width:10px;height:8px;background:#c8d0dc;border-radius:2px}
.entry{position:absolute;left:60px;width:645px;border:1px solid var(--line);border-radius:4px;padding:14px 14px;font-size:8.5px;line-height:13px;color:#222}
.entry h4{font-size:11px;margin-bottom:4px}
.entry .lbl{color:#8a93a3}
.chip{position:absolute;font-size:8px;padding:3px 8px;border-radius:10px}
/* feature */
.feature h2{font-size:29px;font-weight:700}
.feature .sub{font-size:19px;color:#222;margin:20px 0 10px}
.feature p.body{font-size:15px;line-height:27px;color:#333;width:500px}
.shot{overflow:hidden;border-radius:26px 0 0 0}
.mock{position:absolute;background:var(--panel);border-left:16px solid var(--navy)}
.col{position:absolute;background:#e3e3e6;border:1px solid #cfd0d4}
.card{position:absolute;background:#fff;box-shadow:0 6px 18px rgba(0,0,0,.18);font-size:9px;line-height:12px;color:#222;padding:10px}
.card .inner{border:1px solid #d6d8dc;margin-top:28px;height:calc(100% - 40px);padding:8px 10px}
.card ul{padding-left:8px}
/* testimonial */
.quote{font-family:"Syne",sans-serif;font-size:27px;line-height:36px;color:#333;width:580px}
.arrow{width:28px;height:20px}
/* footer */
.fcol h5{font-size:13px;letter-spacing:1px;font-weight:700;color:#222;margin-bottom:14px}
.fcol a{display:block;font-size:15px;color:#444;text-decoration:none;line-height:26px}
.social{width:30px;height:30px;border:1.5px solid #333;border-radius:50%}
</style>
</head>
<body>

<!-- header -->
<div class="abs brand" style="left:111px;top:38px;font-size:26px"><span class="brand-square"></span>Zestora</div>
<nav class="abs nav"><span class="active">Home</span><span>Features ▾</span><span>Solutions</span><span>Pricing</span><span>Resources ▾</span><span>Contact</span></nav>
<a class="btn" style="left:963px;top:40px;width:127px;height:42px">Get Started</a>

<!-- hero -->
<div class="hero-band abs"></div>
<div class="abs display" style="left:0;width:1200px;top:140px;text-align:center;font-size:31px;font-weight:500">Welcome!</div>
<h1 class="abs display" style="left:0;width:1200px;top:178px;text-align:center;font-size:54px;font-weight:700">Reflect. Learn. Grow.</h1>
<p class="abs" style="left:300px;width:600px;top:258px;text-align:center;font-size:19px;line-height:28px;color:#333">A guided journaling experience designed to help you turn reflection into action.</p>
<a class="btn" style="left:493px;top:327px;width:211px;height:41px">Start Journaling Today</a>
<div class="abs dots" style="left:175px;top:365px"></div>
<div class="abs dots" style="left:951px;top:893px"></div>

<div class="abs app">
  <span class="side-icon" style="top:55px;left:-25px"></span>
  <span class="side-icon" style="top:75px;left:-25px"></span>
  <span class="side-icon" style="top:95px;left:-25px"></span>
  <div class="app-body">
    <div class="chip" style="left:60px;top:44px;border:1px solid #bbb;color:#333">+ Add New</div>
    <div class="chip" style="left:672px;top:44px;background:#1fc46f;color:#fff">Gym</div>
    <div class="entry" style="top:80px;height:290px">
      <h4>Thu Aug 22 2024</h4>
      <div class="lbl">What Went Well</div><br>
      Completed all scheduled workouts this week.<br>Increased bench press weight by 10 pounds.<br>Maintained consistent energy levels throughout sessions.<br>
      <div class="lbl">What Didn't Go Well</div>
      Struggled with form on deadlifts, leading to lower back discomfort.<br>Missed two stretching sessions after workouts.<br>Skipped meal prep, resulting in inconsistent nutrition.<br>
      <div class="lbl">Things To Try</div>
      Focus on deadlift form by lowering the weight and reviewing proper technique.<br>Set reminders for post-workout stretching to prevent muscle tightness.<br>Dedicate Sunday evenings to meal prep to ensure a balanced diet.
    </div>
    <div class="entry" style="top:382px;height:100px">
      <h4>Tue Aug 20 2024</h4>
      <div class="lbl">What Went Well</div>
      Achieved a personal best in squats, adding 15 pounds.
    </div>
  </div>
</div>
<div class="abs" role="img" aria-label="Illustration of a person writing with a large pen" style="left:850px;top:660px;width:245px;height:215px;background:linear-gradient(160deg,#f4f6fa,#1b1b1f 70%);border-radius:40% 40% 0 0"></div>

<!-- intro -->
<h2 class="abs display" style="left:0;width:1200px;top:985px;text-align:center;font-size:31px;line-height:41px;font-weight:700">Our journal app is designed to help you reflect<br>on your day in a structured way.</h2>
<p class="abs display" style="left:0;width:1200px;top:1068px;text-align:center;font-size:29px;font-weight:500">Each entry is divided into three sections</p>

<!-- feature 1 -->
<section class="abs feature" style="left:111px;top:1250px">
  <h2 class="display">What Went Well</h2>
  <div class="sub">Celebrate your successes &amp; positive moments.</div>
  <p class="body">Lorem ipsum dolmt, consectetur adipiscing elit, sed do eiusmod tempor incididunt ut labore et dolore magna aliqua. Quis ipsum suspendisse ultrices gravida. Risus c+ommodo viverra maecenas accumsan lacus vel facilisis sed do eiusmod tempor incididunt.</p>
</section>
<a class="btn" style="left:111px;top:1468px;width:126px;height:42px">Learn More</a>
<div class="abs shot" style="left:659px;top:1190px;width:541px;height:392px;background:linear-gradient(135deg,var(--coral),#f9b2a5)">
  <div class="mock" style="left:48px;top:40px;width:500px;height:340px">
    <div class="abs" style="left:48px;top:8px;font-size:10px;font-weight:700">Entry</div>
    <div class="col" style="left:50px;top:60px;width:120px;height:260px"></div>
    <div class="col" style="left:200px;top:60px;width:140px;height:260px"></div>
    <div class="col" style="left:410px;top:60px;width:100px;height:260px"></div>
  </div>
</div>
<div class="abs card" style="left:898px;top:1303px;width:190px;height:330px">
  <b>What Went Well?</b>
  <div class="inner"><ul><li>Completed all scheduled workouts this week.</li><li>Increased bench press weight by 10 pounds.</li><li>Maintained consistent energy levels throughout sessions.</li></ul></div>
</div>
<div class="abs dots" style="left:845px;top:1595px"></div>

<!-- feature 2 -->
<div class="abs" role="img" aria-label="Illustration of a person resting their head on folded arms" style="left:265px;top:1625px;width:285px;height:145px;background:linear-gradient(90deg,#1b1b1f,#cfcfcf 60%,#fff);border-radius:50% 50% 20% 20%"></div>
<div class="abs" style="left:0;top:1755px;width:540px;height:393px;background:linear-gradient(135deg,var(--sun),#fee9b6);border-radius:0 26px 0 0;overflow:hidden">
  <div class="mock" style="left:48px;top:40px;width:480px;height:353px;border-left-width:22px">
    <div class="abs" style="left:48px;top:8px;font-size:10px;font-weight:700">Entry</div>
    <div class="col" style="left:210px;top:60px;width:140px;height:250px"></div>
    <div class="col" style="left:385px;top:60px;width:90px;height:250px"></div>
  </div>
</div>
<div class="abs card" style="left:112px;top:1882px;width:190px;height:330px">
  <b>What Didn't Go Well?</b>
  <div class="inner"><ul><li>Struggled with form on deadlifts, leading to lower back discomfort.</li><li>Missed two stretching sessions after workouts.</li><li>Skipped meal prep, resulting in inconsistent nutrition.</li></ul></div>
</div>
<section class="abs feature" style="left:601px;top:1815px">
  <h2 class="display">What Didn’t Go Well</h2>
  <div class="sub">Acknowledge challenges and areas for improvement.</div>
  <p class="body">Lorem ipsum dolmt, consectetur adipiscing elit, sed do eiusmod tempor incididunt ut labore et dolore magna aliqua. Quis ipsum suspendisse ultrices gravida. Risus c+ommodo viverra maecenas accumsan lacus vel facilisis sed do eiusmod tempor incididunt.</p>
</section>
<a class="btn" style="left:602px;top:2033px;width:126px;height:42px">Learn More</a>

<!-- feature 3 -->
<section class="abs feature" style="left:111px;top:2380px">
  <h2 class="display">Things to Try</h2>
  <div class="sub">Plan actionable steps to make tomorrow even better.</div>
  <p class="body">Lorem ipsum dolmt, consectetur adipiscing elit, sed do eiusmod tempor incididunt ut labore et dolore magna aliqua. Quis ipsum suspendisse ultrices gravida. Risus c+ommodo viverra maecenas accumsan lacus vel facilisis sed do eiusmod tempor incididunt.</p>
</section>
<a class="btn" style="left:111px;top:2599px;width:126px;height:42px">Learn More</a>
<div class="abs shot" style="left:659px;top:2322px;width:541px;height:393px;background:linear-gradient(135deg,#a9c9f7,var(--sky) 60%)">
  <div class="mock" style="left:0;top:48px;width:505px;height:345px;border-left:0;border-right:16px solid #fff0">
    <div class="col" style="left:0;top:70px;width:100px;height:250px"></div>
    <div class="col" style="left:320px;top:70px;width:150px;height:250px"></div>
  </div>
</div>
<div class="abs card" style="left:760px;top:2455px;width:190px;height:330px">
  <b>Things To Try</b>
  <div class="inner"><ul><li>Focus on deadlift form by lowering the weight and reviewing proper technique.</li><li>Set reminders for post-workout stretching to prevent muscle tightness.</li><li>Dedicate Sunday evenings to meal prep to ensure a balanced diet.</li></ul></div>
</div>

<!-- testimonials -->
<h2 class="abs display" style="left:0;width:1200px;top:2925px;text-align:center;font-size:31px;font-weight:700">Client Testimonials</h2>
<p class="abs" style="left:280px;width:640px;top:2978px;text-align:center;font-size:14.5px;line-height:27px;color:#444">Lorem ipsum dolor sit amet, consectetur adipiscing elit, sed do eiusmod tempor incididunt ut labore et dolore magna aliqua.</p>
<svg class="abs arrow" style="left:48px;top:3160px" viewBox="0 0 28 20"><path d="M27 10H2M10 2 2 10l8 8" fill="none" stroke="#888" stroke-width="2"/></svg>
<svg class="abs arrow" style="left:1124px;top:3160px" viewBox="0 0 28 20"><path d="M1 10h25M18 2l8 8-8 8" fill="none" stroke="#222" stroke-width="2"/></svg>
<div class="abs" style="left:145px;top:3068px;width:204px;height:204px;border:3px dotted #b9cdf0;border-radius:50%"></div>
<div class="abs" role="img" aria-label="Portrait photo of the client" style="left:180px;top:3103px;width:134px;height:134px;border-radius:50%;background:linear-gradient(160deg,#cdd6c4,#8a6a4e)"></div>
<div class="abs display" style="left:423px;top:3080px;font-size:40px;font-weight:800">“</div>
<div class="abs" style="left:482px;top:3074px;color:#f6b800;font-size:17px;letter-spacing:1px">★★★★★</div>
<p class="abs quote" style="left:482px;top:3100px">Sed ut perspiciatis unde omnis iste natus error sit voluptatem accusan doloremque laudantium, totam rem aperiam.</p>
<div class="abs display" style="left:960px;top:3210px;font-size:40px;font-weight:800">”</div>
<div class="abs display" style="left:482px;top:3237px;font-size:18px;font-weight:700">Marten Hollis</div>
<div class="abs" style="left:482px;top:3264px;font-size:14px;color:#555">Lorem Ipsum</div>

<!-- AI coach -->
<div class="coach-band abs"></div>
<div class="abs" role="img" aria-label="Faint circuit-line decoration" style="left:780px;top:3360px;width:420px;height:370px;background:radial-gradient(circle at 60% 50%,#d9e6fa,transparent 70%)"></div>
<h2 class="abs display" style="left:0;width:1200px;top:3490px;text-align:center;font-size:31px;line-height:40px;font-weight:700">Your Personal<br>AI Coach</h2>
<p class="abs" style="left:260px;width:680px;top:3575px;text-align:center;font-size:14.5px;line-height:27px;color:#333">Get ready to take your journaling experience to the next level with our upcoming AI Coach feature. Drawing insights from your past entries, the AI Coach will offer personalized guidance, helping you identify patterns and make meaningful progress in your life.</p>
<a class="btn" style="left:492px;top:3687px;width:211px;height:40px">Start Journaling Today</a>
<div class="abs" role="img" aria-label="Illustration of a person working on a laptop" style="left:0;top:3660px;width:270px;height:265px;background:linear-gradient(200deg,#f4f6fa,#1b1b1f 65%);border-radius:0 50% 0 0"></div>

<!-- footer -->
<div class="abs" style="left:0;top:3830px;width:1200px;border-top:1px solid var(--line)"></div>
<div class="abs brand" style="left:111px;top:3918px;font-size:34px;font-weight:400"><span class="brand-square" style="width:46px;height:46px"></span>Zestora</div>
<div class="abs fcol" style="left:424px;top:3880px"><h5>QUICK LINKS</h5><a>Home</a><a>Pricing</a><a>Features</a><a>Solutions</a></div>
<div class="abs fcol" style="left:647px;top:3880px"><h5>OTHER LINKS</h5><a>Resources</a><a>Contact Us</a><a>Terms &amp; Conditions</a><a>Privacy Policy</a></div>
<div class="abs fcol" style="left:907px;top:3880px">
  <h5>CONTACT US</h5>
  <svg class="abs" style="left:0;top:36px" width="14" height="18" viewBox="0 0 14 18"><path d="M7 0a7 7 0 0 0-7 7c0 5 7 11 7 11s7-6 7-11a7 7 0 0 0-7-7zm0 10a3 3 0 1 1 0-6 3 3 0 0 1 0 6z" fill="#222"/></svg>
  <a style="margin-left:31px">Zestora,<br>Address Comes Here</a>
  <svg class="abs" style="left:0;top:92px" width="15" height="15" viewBox="0 0 24 24"><path d="M6.6 10.8a15 15 0 0 0 6.6 6.6l2.2-2.2c.3-.3.7-.4 1-.2 1.1.4 2.3.6 3.6.6.6 0 1 .4 1 1V20c0 .6-.4 1-1 1A17 17 0 0 1 3 4c0-.6.4-1 1-1h3.5c.6 0 1 .4 1 1 0 1.3.2 2.5.6 3.6.1.3 0 .7-.2 1z" fill="#222"/></svg>
  <a style="margin-left:31px;margin-top:6px">+1-555-014-2290</a>
  <svg class="abs" style="left:0;top:126px" width="16" height="12" viewBox="0 0 16 12"><rect width="16" height="12" rx="1" fill="#222"/><path d="M1 1l7 5 7-5" stroke="#fff" fill="none"/></svg>
  <a style="margin-left:31px;margin-top:6px">info@zestora.com</a>
</div>
<div class="abs" style="left:111px;top:4073px;width:978px;border-top:1px solid var(--line)"></div>
<div class="abs" style="left:111px;top:4100px;font-size:14px;color:#333">2024 Zestora. All Rights Reserved.</div>
<div class="abs" style="left:902px;top:4096px;display:flex;gap:9px">
  <span class="social"></span><span class="social"></span><span class="social"></span><span class="social"></span><span class="social"></span>
</div>

</body>
</html>
```